Harwick Moss Fine Art gallery website - Modern british art for sale

We need a website design that is both current and high end. Our products are expensive and this should be reflected in the look of the website. We would like the logo we had designed last year to be clearly seen in the design. We want sleek, simple, and easy to navigate. Nothing too colourful as the colours of the art should always take precedence.

Target Market(s)

The average price of one our products starts at £250 and can go up to £10,000 we are an entry level gallery.

Industry/Entity Type

Art Gallery

Number of Pages Required

5+ page

Font styles to use
Sans Serif

Colors
000000
ffffff
faa54b
abd037
886aae
b868aa

Requirements
Must have
• Attractive front page. Linked to our Updates feed.
• 4 links from front page - New Releases, about us, Artists, contact us
• Social media links - Journal, Updates, YouTube, Gallery.
• Each artist must have their own page, each page must have a biography link to another page.
Nice to have
• Utilise our new logo design. I would like the Updates feed to link to the front page in a small way so you can see what's being said on Updates by the company. For future proofing maybe have a locations function on the front page which can be adroit down menu showing where our other galleries are.

```html
<!DOCTYPE html>
<html lang="en">
<head>
<meta charset="utf-8">
<title>Harwick Moss Fine Art</title>
<link href="https://fonts.googleapis.com/css2?family=Jost:wght@300;400;500;600&family=Oswald:wght@400;500&family=Arimo:wght@400;700&display=swap" rel="stylesheet">
<style>
:root{
  --navy:#07121c;
  --navy-soft:#0d1b27;
  --cyan:#3fb0d4;
  --button:#4b97b5;
  --charcoal:#2a2a2a;
  --ink:#111;
  --grey-text:#8a8a8a;
  --white:#fff;
}
*{box-sizing:border-box;margin:0;padding:0}
html,body{width:1200px;height:2871px;overflow:hidden}
body{position:relative;font-family:'Jost',sans-serif;color:var(--ink);background:var(--white)}
.abs{position:absolute}

/* Hero */
.hero{left:0;top:0;width:1200px;height:521px;background:var(--navy)}
.hero-art{left:0;top:150px;width:1200px;height:371px;
  background:linear-gradient(180deg,var(--navy) 0%,rgba(7,18,28,.6) 30%,rgba(7,18,28,0) 60%),
  linear-gradient(100deg,#2a4f6b 0%,#b34a3a 35%,#3a8fb0 60%,#c7563e 80%,#2b5a74 100%)}
.brand{left:184px;top:44px;color:var(--white);font-size:23px;font-weight:400;line-height:1;display:flex;align-items:center;gap:9px;white-space:nowrap}
.brand-mark{width:12px;height:12px;border:2px solid var(--white);border-radius:50%;flex:none}
.nav a{position:absolute;top:55px;color:var(--white);font-size:12px;letter-spacing:1.6px;text-decoration:none;font-weight:400;white-space:nowrap}
.nav a.current{font-weight:600}
.nav a.current::after{content:"";position:absolute;left:0;right:0;top:22px;height:2px;background:var(--cyan)}
.social{display:flex;gap:12px;align-items:center}
.social a{color:var(--white);font-size:11px;letter-spacing:1.2px;text-decoration:none;font-weight:400;white-space:nowrap}
.hero h1{left:186px;top:172px;color:var(--white);font-weight:500;font-size:39px;letter-spacing:2px;white-space:nowrap}
.hero p{left:187px;top:244px;width:560px;color:#e6ecf0;font-size:17px;line-height:30px;letter-spacing:1.8px;font-weight:300}

/* Section headings */
.section-title{font-family:'Oswald',sans-serif;font-weight:400;font-size:32px;letter-spacing:.5px;display:flex;align-items:center;gap:14px;white-space:nowrap}
.section-title::before,.section-title::after{content:"";width:90px;height:3px;background:var(--button)}
.section-title.wide::before,.section-title.wide::after{width:180px}

/* About */
.about{left:0;top:521px;width:1200px;height:461px;background:linear-gradient(180deg,#ececec,#d9d9d9)}
.about .section-title{left:184px;top:26px}
.about-lead{left:184px;top:106px;width:350px;font-family:'Arimo',sans-serif;font-weight:700;font-size:14px;line-height:21px}
.about-copy{left:184px;width:350px;color:var(--grey-text);font-size:12px;line-height:19px}
.tweets{left:637px;top:59px;width:307px;height:363px;background:rgba(240,240,240,.9);border:1px solid #c8c8c8;font-family:'Arimo',sans-serif}
.tweets-head{position:absolute;left:12px;top:10px;font-weight:700;font-size:17px}
.follow{position:absolute;right:6px;top:8px;height:22px;padding:0 8px;border:1px solid #bbb;border-radius:3px;background:#f7f7f7;font-size:11px;font-weight:700;line-height:20px;white-space:nowrap}
.tweet-list{position:absolute;left:8px;top:42px;width:280px;height:278px;overflow:hidden}
.tweet{display:flex;gap:10px;padding:8px 0 10px;font-size:12px;line-height:16px;border-bottom:1px solid #ddd}
.tweet-avatar{width:48px;height:48px;background:#fff;border:1px solid #ddd;flex:none}
.tweet-body{flex:1}
.tweet b{font-size:13px}
.tweet-date{float:right;font-size:11px;color:#444}
.scrollbar{position:absolute;right:4px;top:42px;width:8px;height:278px;background:#ddd}
.scrollbar::before{content:"";position:absolute;left:1px;top:2px;width:6px;height:34px;background:#aaa;border-radius:3px}
.tweet-box{position:absolute;left:3px;bottom:3px;width:299px;height:34px;background:#fff;border:1px solid #ccc;font-size:12px;color:#555;padding:8px 10px}

/* Releases */
.releases{left:0;top:982px;width:1200px;height:721px;background:var(--charcoal)}
.releases .section-title{left:0;top:30px;width:1200px;justify-content:center;color:var(--white)}
.releases-intro{left:184px;top:96px;width:834px;text-align:center;color:#d7d7d7;font-size:14px;line-height:24px}
.artwork{width:193px;height:174px;border:3px solid var(--cyan)}
.btn{background:var(--button);color:var(--white);font-family:'Oswald',sans-serif;font-size:14px;letter-spacing:1px;display:flex;align-items:center;justify-content:center;border-radius:2px}

/* Artists */
.artists{left:0;top:1703px;width:1200px;height:588px;background:linear-gradient(180deg,#f0f0f0,#e2e2e2)}
.artists .section-title{left:0;top:30px;width:1200px;justify-content:center}
.portrait{width:189px;height:189px;border:4px solid var(--white);box-shadow:0 1px 3px rgba(0,0,0,.25)}
.artist-name{font-family:'Oswald',sans-serif;font-size:17px;letter-spacing:1.5px;white-space:nowrap}
.artist-bio{width:200px;color:var(--grey-text);font-size:12px;line-height:20px}
.learn{width:109px;height:27px;border:2px solid var(--cyan);background:var(--white);font-family:'Oswald',sans-serif;font-size:13px;letter-spacing:.5px;display:flex;align-items:center;justify-content:center}

/* Contact */
.contact{left:0;top:2291px;width:1200px;height:515px;background:linear-gradient(110deg,#1f4a55 0%,#3b6270 30%,#6b4a3a 55%,#2a5a66 80%)}
.map{left:0;top:0;width:1200px;height:515px;clip-path:polygon(890px 0,1200px 0,1200px 515px,765px 515px);background:linear-gradient(160deg,#cfd8c8,#9fb7c9 60%,#7a9fbd)}
.contact .section-title{left:0;top:30px;width:1200px;justify-content:center;color:var(--white)}
.contact-line{color:#dfe7ea;font-size:13px;line-height:22px;display:flex;gap:22px;align-items:flex-start}
.contact-line svg{flex:none}
.field{border-bottom:1px solid #9fb3ba;color:#b9c6ca;font-size:11px;padding-bottom:6px}
.message{border:2px solid var(--cyan);color:#b9c6ca;font-size:11px;padding:6px 8px}

/* Footer */
.footer{left:0;top:2806px;width:1200px;height:65px;background:var(--navy-soft)}
.copyright{left:197px;top:26px;color:var(--white);font-size:9px}
.footer-social{right:184px;top:24px;display:flex;gap:18px;align-items:center}
.follow-us{color:var(--white);font-size:9px;letter-spacing:.5px}
</style>
</head>
<body>

<header class="abs hero">
  <div class="abs hero-art" role="img" aria-label="Colourful street art mural in blue, red and orange"></div>
  <div class="abs brand"><span class="brand-mark"></span>Harwick Moss Fine Art</div>
  <nav class="nav">
    <a href="#" class="current" style="left:488px">HOME</a>
    <a href="#" style="left:570px">ABOUT US</a>
    <a href="#" style="left:681px">NEW RELEASES</a>
    <a href="#" style="left:833px">ARTISTS</a>
    <a href="#" style="left:934px">CONTACT US</a>
  </nav>
  <div class="abs social" style="right:184px;top:20px" aria-label="Social media links"><a href="#">JOURNAL</a><a href="#">UPDATES</a><a href="#">GALLERY</a></div>
  <h1 class="abs">Welcome to Harwick Moss Fine Art</h1>
  <p class="abs">We've been on the web since our information in the year 2000 and in our 10th Year of Business we find an ever progressing internet demanding another change in our Website. We hope that you like what we've done.</p>
</header>

<section class="abs about">
  <h2 class="abs section-title">ABOUT US</h2>
  <p class="abs about-lead">Lorem ipsum dolor sit amet, ei dicit persius molestiae usu, vide soluta evertitur e</p>
  <p class="abs about-copy" style="top:178px">Has, ei vix debet philosophia. Viris nullam sententiae mel id. Eu bonorum eruditi voluptatibus est, ipsum quodsi discere id his. Has at primis reprehendunt, ex sit ludus habemus maluisset, mea id illud quidam salutatus.</p>
  <p class="abs about-copy" style="top:286px">At invenire salutatus sed, consequuntur reprehendunt an vis. Cum meis laudem id, postulant democritum voluptaria cu quo, has at illud sonet dictas. Menandri deserunt delicatissimi ad eam. Nam at summo decore, eu modus vivendo maluisset vix.</p>
  <aside class="abs tweets">
    <div class="tweets-head">Tweets</div>
    <div class="follow">Follow @harwickmossart</div>
    <div class="tweet-list">
      <div class="tweet"><div class="tweet-avatar"></div><div class="tweet-body"><span class="tweet-date">16 Nov</span><b>Harwick Moss</b><br>@harwickmossart<br>Lorem ipsum dolor sit amet, consectetuer adipiscing elit, sed diam nonummy nibh euismod.</div></div>
      <div class="tweet"><div class="tweet-avatar"></div><div class="tweet-body"><span class="tweet-date">16 Nov</span><b>Harwick Moss</b><br>@harwickmossart<br>Lorem ipsum dolor sit amet, consectetuer adipiscing elit, sed diam nonummy nibh euismod.</div></div>
      <div class="tweet"><div class="tweet-avatar"></div><div class="tweet-body"><span class="tweet-date">16 Nov</span><b>Harwick Moss</b><br>@harwickmossart<br>Lorem ipsum dolor sit amet.</div></div>
    </div>
    <div class="scrollbar"></div>
    <div class="tweet-box">Tweet to @harwickmossart</div>
  </aside>
</section>

<section class="abs releases">
  <h2 class="abs section-title wide">NEW RELEASES</h2>
  <p class="abs releases-intro">At invenire salutatus sed, consequuntur reprehendunt an vis. Cum meis laudem id, postulant democritum voluptaria cu quo, has at illud sonet dictas. Menandri deserunt delicatissimi ad eam. Nam at summo decore, eu modus vivendo maluisset vix.</p>
  <div class="abs artwork" style="left:184px;top:189px;background:linear-gradient(135deg,#f07a4a,#b07ad0 50%,#e8d060)" role="img" aria-label="Abstract artwork with orange, violet and yellow waves"></div>
  <div class="abs artwork" style="left:398px;top:189px;background:linear-gradient(180deg,#f4f1ea,#c9c4bb 60%,#e0793a)" role="img" aria-label="Ink drawing of a cathedral tower with an orange building"></div>
  <div class="abs artwork" style="left:612px;top:189px;background:linear-gradient(135deg,#f2f2f2,#9a9a9a)" role="img" aria-label="Black and white line drawing of swirling forms"></div>
  <div class="abs artwork" style="left:825px;top:189px;background:linear-gradient(180deg,#c9ccc6,#8fa7a3 50%,#c8c6b8)" role="img" aria-label="Muted print of a teal globe"></div>
  <div class="abs artwork" style="left:184px;top:394px;background:linear-gradient(180deg,#f3f3f3,#b8b8b8)" role="img" aria-label="Grey sketch of sculptural figures"></div>
  <div class="abs artwork" style="left:398px;top:394px;background:linear-gradient(90deg,#3a4aa0,#c03060 35%,#e8c040 70%,#f0a030)" role="img" aria-label="Vertical colour stripes artwork"></div>
  <div class="abs artwork" style="left:612px;top:394px;background:linear-gradient(135deg,#f2f2f2,#9a9a9a)" role="img" aria-label="Black and white line drawing of swirling forms"></div>
  <div class="abs artwork" style="left:825px;top:394px;background:linear-gradient(180deg,#c9ccc6,#8fa7a3 50%,#c8c6b8)" role="img" aria-label="Muted print of a teal globe"></div>
  <a class="abs btn" style="left:536px;top:629px;width:128px;height:42px">SEE MORE</a>
</section>

<section class="abs artists">
  <h2 class="abs section-title">ARTISTS</h2>

  <div class="abs portrait" style="left:184px;top:129px;background:linear-gradient(180deg,#c9b9a8,#8a7060)" role="img" aria-label="Portrait photo of artist Nora Pellingham"></div>
  <div class="abs artist-name" style="left:398px;top:128px">Nora Pellingham</div>
  <p class="abs artist-bio" style="left:398px;top:164px">Has, ei vix debet philosophia. Viris nullam sententiae mel id. Eu bonorum eruditi voluptatibus est, ipsum quodsi discere id his.</p>
  <a class="abs learn" style="left:398px;top:291px">LEARN MORE</a>

  <div class="abs portrait" style="left:612px;top:129px;background:linear-gradient(180deg,#e0e0e0,#9a8a7e)" role="img" aria-label="Portrait photo of artist Arthur Wendle"></div>
  <div class="abs artist-name" style="left:827px;top:128px">Arthur Wendle</div>
  <p class="abs artist-bio" style="left:827px;top:164px">Has, ei vix debet philosophia. Viris nullam sententiae mel id. Eu bonorum eruditi voluptatibus est, ipsum quodsi discere id his.</p>
  <a class="abs learn" style="left:827px;top:291px">LEARN MORE</a>

  <div class="abs portrait" style="left:184px;top:349px;background:linear-gradient(180deg,#d8d8d8,#5a4030)" role="img" aria-label="Portrait photo of artist Simon Crale"></div>
  <div class="abs artist-name" style="left:398px;top:348px">Simon Crale</div>
  <p class="abs artist-bio" style="left:398px;top:384px">Has, ei vix debet philosophia. Viris nullam sententiae mel id. Eu bonorum eruditi voluptatibus est, ipsum quodsi discere id his.</p>
  <a class="abs learn" style="left:398px;top:511px">LEARN MORE</a>

  <div class="abs portrait" style="left:612px;top:349px;background:linear-gradient(180deg,#9a9a90,#4a7a5a)" role="img" aria-label="Portrait photo of artist Oliver Tamsett"></div>
  <div class="abs artist-name" style="left:827px;top:348px">Oliver Tamsett</div>
  <p class="abs artist-bio" style="left:827px;top:384px">Has, ei vix debet philosophia. Viris nullam sententiae mel id. Eu bonorum eruditi voluptatibus est, ipsum quodsi discere id his.</p>
  <a class="abs learn" style="left:827px;top:511px">LEARN MORE</a>
</section>

<section class="abs contact" role="img" aria-label="Weathered teal and rust painted wall texture">
  <div class="abs map" role="img" aria-label="Street map showing the gallery location"></div>
  <h2 class="abs section-title">CONTACT US</h2>
  <div class="abs contact-line" style="left:184px;top:88px">
    <svg width="14" height="20" viewBox="0 0 14 20"><path d="M7 0a7 7 0 0 1 7 7c0 5-7 13-7 13S0 12 0 7a7 7 0 0 1 7-7z" fill="#4b97b5"/><circle cx="7" cy="7" r="2.5" fill="#2a4a55"/></svg>
    <span>Vas, ei vix debet philosophia.<br>Viris nullam sententiae mel id. Eu bonorum eruditi</span>
  </div>
  <div class="abs contact-line" style="left:184px;top:156px">
    <svg width="20" height="20" viewBox="0 0 20 20"><path d="M4 1l4 4-2 3c1 3 3 5 6 6l3-2 4 4-3 3C8 19 1 12 1 4z" fill="#4b97b5"/></svg>
    <span>(123) 555-0142</span>
  </div>
  <div class="abs contact-line" style="left:184px;top:212px">
    <svg width="28" height="20" viewBox="0 0 28 20"><rect width="28" height="20" fill="#4b97b5"/><path d="M0 0l14 11L28 0" fill="none" stroke="#2a4a55" stroke-width="2"/></svg>
    <span>harwickmoss@youremail.com</span>
  </div>
  <div class="abs field" style="left:184px;top:292px;width:189px">Name</div>
  <div class="abs field" style="left:402px;top:292px;width:188px">Email</div>
  <div class="abs message" style="left:184px;top:325px;width:406px;height:85px">Your message</div>
  <a class="abs btn" style="left:184px;top:433px;width:130px;height:40px">SEND</a>
</section>

<footer class="abs footer">
  <div class="abs copyright">Copyright 2017 Harwick Moss Fine Art. All rights reserved.</div>
  <div class="abs footer-social">
    <span class="follow-us">FOLLOW US</span>
    <div class="social" aria-label="Social media links"><a href="#">JOURNAL</a><a href="#">UPDATES</a><a href="#">GALLERY</a></div>
  </div>
</footer>

</body>
</html>
```